Rig up a website for a Rigging Company

We already have a logo. Looking for a website design that works on pavlune.com.
Our rigging company uses semi trucks, forklifts, and similar equipment to move large machines.
Our logo is white, black and red.

Target Market(s)

Medical Industry (moving medical equipment), Utility Industry (power equipment), Food Industry (moving bottling/packing equipment), US Government (large equipment)

Industry/Entity Type

It Company

Coding

Coded - Design and coding required

Number of Pages Required

5+ page

Font styles to use
Sans Serif

Colors
ec1f27
ffffff
0355a3

Requirements
Must have
• Home page, About page, Services Page, and Contact Information page
Nice to have
• Pictures of semi and forklifts and ability to insert our own pictures of our equipment

```html
<!DOCTYPE html>
<html lang="en">
<head>
<meta charset="utf-8">
<title>Halvard Rigging</title>
<link href="https://fonts.googleapis.com/css2?family=Barlow:wght@400;500;600&display=swap" rel="stylesheet">
<style>
:root{
  --red:#e4161d;
  --black:#000;
  --ink:#1a1a1a;
  --grey-text:#333;
  --footer-bg:#ececec;
  --footer-bar:#dcdcdc;
  --line:#cfcfcf;
  --white:#fff;
  --olive:#8a9a1a;
}
*{box-sizing:border-box;margin:0;padding:0}
html,body{width:710px;height:1200px;overflow:hidden;background:var(--white)}
body{position:relative;font-family:"Barlow",sans-serif;color:var(--ink)}
.abs{position:absolute}

.topbar{left:0;top:0;width:710px;height:18px;background:var(--black);color:var(--white);font-size:7px}
.topbar .contact{left:68px;top:5px;display:flex;gap:8px;align-items:center}
.topbar .search{left:542px;top:5px;color:#777;font-size:7px;letter-spacing:.5px}
.topbar .search-line{left:540px;top:3px;width:66px;height:12px;border-right:1px solid #333}
.topbar .social{top:2px;width:14px;height:14px;background:#222}

.header{left:0;top:18px;width:710px;height:51px;background:linear-gradient(#fff,#e9e9e9)}
.brand{left:78px;top:16px;font-size:15px;font-weight:600;color:var(--black);letter-spacing:.5px;display:flex;align-items:center;gap:5px}
.brand .mark{width:10px;height:10px;background:var(--red)}
.nav-item{top:15px;text-align:center;font-size:9px;letter-spacing:.4px;line-height:1.2}
.nav-item small{display:block;font-size:6px;letter-spacing:0;color:#333}
.nav-sep{top:12px;width:1px;height:26px;background:#d6d6d6}
.btn{display:flex;align-items:center;justify-content:center;gap:5px;color:var(--white);font-size:9px;font-weight:500;letter-spacing:.3px}
.btn-apply{left:458px;top:14px;width:85px;height:22px;background:var(--red)}
.btn-contact{left:557px;top:14px;width:85px;height:22px;background:var(--black)}

.hero{left:0;top:69px;width:710px;height:317px;background:linear-gradient(160deg,#5d88c4 0%,#9fbde0 45%,#cfd9e4 75%,#b9a78a 100%)}
.hero-title{left:382px;top:110px;width:242px;text-align:center;font-size:18px;letter-spacing:.5px;color:var(--black)}
.hero-sub{left:382px;top:135px;width:242px;text-align:center;font-size:8.5px;color:var(--black)}
.btn-start{left:466px;top:164px;width:85px;height:21px;background:var(--red)}
.frame{width:100px;height:100px;border:6px solid var(--black);background:linear-gradient(135deg,#c9d3dc,#8d2a2a 70%,#e0e0e0)}
.frame-label{color:var(--white);font-size:9px;font-weight:500}
.down{left:615px;top:309px;width:26px;height:26px;border:1.5px solid var(--white);border-radius:50%}

.services{left:58px;top:345px;width:594px;height:165px;display:flex}
.service{flex:1;color:var(--white);text-align:center;padding:0 16px}
.service.red{background:var(--red)}
.service.dark{background:var(--black);border-left:1px solid #222}
.service h3{font-size:9px;font-weight:500;letter-spacing:.3px;margin-top:20px}
.service svg{margin:12px auto 10px;display:block}
.service p{font-size:6.4px;line-height:13.5px}

.rule{left:58px;width:594px;height:1px;background:var(--line)}
.section-title{font-size:11.5px;font-weight:500;color:var(--black)}

.gallery .shot{top:601px;height:108px}
.gallery .shot.feature{top:588px;height:134px}
.g-arrow{top:650px;width:10px;height:10px;color:#fff;font-size:10px}

.about-text{left:59px;top:804px;width:228px;font-size:7.4px;line-height:12.1px;text-align:justify;color:var(--grey-text)}
.about-img{left:300px;top:792px;width:150px;height:126px;background:linear-gradient(#9aa2ac,#5b6168 60%,#2b2d31)}
.btn-read{left:58px;top:934px;width:70px;height:22px;background:var(--red)}

.call{left:466px;width:186px;height:47px;color:var(--white)}
.call svg.bg{position:absolute;left:0;top:0}
.call .label{position:absolute;left:32px;top:8px;font-size:8px;font-weight:500}
.call .num{position:absolute;left:32px;top:18px;font-size:13px;letter-spacing:.3px}
.call .icon{position:absolute;right:28px;top:14px}

.footer{left:0;top:980px;width:710px;height:200px;background:var(--footer-bg)}
.footer h4{position:absolute;top:18px;font-size:11.5px;font-weight:500;letter-spacing:.3px;color:var(--black)}
.links{position:absolute;left:82px;top:48px;list-style:none;font-size:6.5px;line-height:15.2px}
.links li::before{content:"›";margin-right:6px}
.quote{position:absolute;left:198px;top:36px;width:130px;height:78px;background:#d9d9d9;border-radius:5px;padding:9px 10px;font-size:6.2px;line-height:12px;color:#555;text-align:justify}
.quote-tail{position:absolute;left:210px;top:114px;width:0;height:0;border-left:7px solid transparent;border-right:7px solid transparent;border-top:8px solid #d9d9d9}
.avatar{position:absolute;left:218px;top:122px;width:28px;height:28px;border-radius:50%;background:#8a6f5a}
.author{position:absolute;left:254px;top:127px;font-size:7px;line-height:9px;color:var(--olive);font-weight:500}
.field{position:absolute;left:370px;width:124px;height:17px;background:var(--white);border:1px solid #c8c8c8;font-size:6px;padding:4px 8px;color:#444}
.btn-submit{left:370px;top:139px;width:48px;height:18px;background:var(--red);font-size:7px}
.follow{position:absolute;left:530px;font-size:6.5px;display:flex;align-items:center;gap:10px}
.follow span.sq{width:16px;height:16px}
.bottombar{left:0;top:1180px;width:710px;height:20px;background:var(--footer-bar);text-align:center;font-size:6.3px;letter-spacing:.5px;line-height:20px;color:#333}
</style>
</head>
<body>

<div class="abs topbar">
  <div class="abs contact">
    <span>&#9743; 1-800 555 0142</span><span>|</span><span>&#9993; hello@halvardrig.com</span>
  </div>
  <div class="abs search-line"></div>
  <div class="abs search">SEARCH</div>
  <svg class="abs" style="left:598px;top:4px" width="10" height="10" viewBox="0 0 10 10"><circle cx="4" cy="4" r="3" fill="none" stroke="#bbb" stroke-width="1.3"/><line x1="6.2" y1="6.2" x2="9" y2="9" stroke="#bbb" stroke-width="1.4"/></svg>
  <span class="abs social" style="left:614px"></span>
  <span class="abs social" style="left:631px"></span>
</div>

<header class="abs header">
  <div class="abs brand"><span class="mark"></span>HALVARD RIGGING</div>
  <div class="abs nav-item" style="left:236px;width:70px">HOME<small>Welcome Text!</small></div>
  <div class="abs nav-sep" style="left:309px"></div>
  <div class="abs nav-item" style="left:312px;width:70px">SERVICES<small>Need Help</small></div>
  <div class="abs nav-sep" style="left:381px"></div>
  <div class="abs nav-item" style="left:381px;width:70px">PRODUCTS<small>Gallery</small></div>
  <div class="abs btn btn-apply">
    <svg width="8" height="9" viewBox="0 0 8 9"><rect x="0.5" y="0.5" width="7" height="8" fill="none" stroke="#fff"/><line x1="2" y1="3" x2="6" y2="3" stroke="#fff"/><line x1="2" y1="5" x2="6" y2="5" stroke="#fff"/></svg>APPLY NOW
  </div>
  <div class="abs btn btn-contact">
    <svg width="8" height="8" viewBox="0 0 8 8"><path d="M1 1 L3 1 L3.6 2.8 L2.6 3.6 Q3.5 5 4.6 5.6 L5.4 4.6 L7 5.2 L7 7 Q3 7 1 1Z" fill="#fff"/></svg>CONTACT US
  </div>
</header>

<section class="abs hero" role="img" aria-label="Yellow mobile crane lifting a concrete beam under a blue cloudy sky">
</section>
<div class="abs frame" role="img" aria-label="Red semi truck" style="left:78px;top:120px;transform:rotate(-20deg)"></div>
<div class="abs frame" role="img" aria-label="Green forklift in a warehouse" style="left:76px;top:220px;width:106px;height:106px;transform:rotate(22deg);background:linear-gradient(135deg,#2f4f8c,#6c83b8 50%,#9bd14a 85%)"></div>
<div class="abs frame-label" style="left:174px;top:126px">SEMI TRUCKS</div>
<div class="abs frame-label" style="left:38px;top:223px">FORKLIFTS</div>
<div class="abs hero-title">HALVARD RIGGING</div>
<div class="abs hero-sub">Neque porro quisquam est qui dolorem ipsum quia</div>
<div class="abs btn btn-start">
  <svg width="9" height="9" viewBox="0 0 9 9"><circle cx="4.5" cy="4.5" r="4.3" fill="#fff"/><path d="M3.5 2.5 L5.5 4.5 L3.5 6.5" fill="none" stroke="#e4161d" stroke-width="1.3"/></svg>GET STARTED
</div>
<div class="abs down"><svg width="23" height="23" viewBox="0 0 23 23"><path d="M7 9.5 L11.5 14 L16 9.5" fill="none" stroke="#fff" stroke-width="1.5"/></svg></div>

<section class="abs services">
  <article class="service red">
    <h3>SEMI TRUCKS</h3>
    <svg width="48" height="24" viewBox="0 0 48 24" fill="none" stroke="#fff" stroke-width="2"><path d="M2 17 V6 H12 L17 11 H20 V3 H44 V17 Z"/><circle cx="9" cy="19" r="3" fill="#e4161d"/><circle cx="30" cy="19" r="3" fill="#e4161d"/><circle cx="38" cy="19" r="3" fill="#e4161d"/></svg>
    <p>Lorem ipsum dolor sit amet, consectetur adipiscing elit, sed do eiusmod tempor incididunt ut labore et dolore magna aliqua. Duis aute irure dolor in reprehenderit in voluptate velit...</p>
  </article>
  <article class="service dark">
    <h3 style="margin-top:18px">FORKLIFTS</h3>
    <svg width="36" height="26" viewBox="0 0 36 26" fill="#fff"><rect x="4" y="10" width="16" height="9"/><path d="M8 10 V3 H15 L18 10" fill="none" stroke="#fff" stroke-width="2"/><rect x="23" y="1" width="2" height="20"/><rect x="23" y="19" width="11" height="2"/><circle cx="8" cy="21" r="3.5"/><circle cx="18" cy="21" r="3.5"/></svg>
    <p>Lorem ipsum dolor sit amet, consectetur adipiscing elit, sed do eiusmod tempor incididunt ut labore et dolore magna aliqua. Duis aute irure dolor in reprehenderit in voluptate velit...</p>
  </article>
  <article class="service dark">
    <h3 style="margin-top:24px">LARGE MACHINES</h3>
    <svg width="52" height="26" viewBox="0 0 52 26" fill="none" stroke="#fff" stroke-width="2" style="margin-top:4px"><path d="M2 19 V11 H10 L14 6 H24 V12 H42 V19 Z"/><path d="M24 12 L46 3 L49 6"/><circle cx="10" cy="21" r="3" fill="#000"/><circle cx="34" cy="21" r="3" fill="#000"/></svg>
    <p>Lorem ipsum dolor sit amet, consectetur adipiscing elit, sed do eiusmod tempor incididunt ut labore et dolore magna aliqua. Duis aute irure dolor in reprehenderit in voluptate velit...</p>
  </article>
</section>

<div class="abs rule" style="top:535px"></div>
<h2 class="abs section-title" style="left:0;width:710px;text-align:center;top:545px">Product Gallery</h2>

<div class="gallery">
  <div class="abs shot" role="img" aria-label="Yellow forklift carrying boxes in a warehouse" style="left:0;width:178px;background:linear-gradient(#e8e8e8,#cfcfcf 60%,#c9a53a 85%,#f2f2f2)"></div>
  <div class="abs shot" role="img" aria-label="Backhoe loader against a blue sky" style="left:178px;width:156px;background:linear-gradient(#4a74b3,#6d8fc0 50%,#8a7a45 80%,#333)"></div>
  <div class="abs shot feature" role="img" aria-label="Red semi truck on a highway at sunset" style="left:334px;width:220px;background:linear-gradient(#6f7891,#d9a58e 40%,#b84a3e 62%,#444 78%,#2b2b2b)"></div>
  <div class="abs shot" role="img" aria-label="Worker driving a forklift in a storage area" style="left:554px;width:156px;background:linear-gradient(90deg,#7a4650,#c59aa3 50%,#3a5f8a)"></div>
  <div class="abs g-arrow" style="left:10px">‹</div>
  <div class="abs g-arrow" style="left:693px">›</div>
</div>

<div class="abs rule" style="top:756px"></div>

<h2 class="abs section-title" style="left:59px;top:778px">About Our Company</h2>
<p class="abs about-text">Sed ut perspiciatis unde omnis iste natus error sit voluptatem accusantium doloremque laudantium, totam rem aperiam, eaque ipsa quae ab illo inventore veritatis et quasi architecto beatae vitae dicta sunt explicabo. Nemo enim ipsam voluptatem quia voluptas sit aspernatur aut odit aut fugit, sed quia consequuntur magni dolores eos qui ratione voluptatem sequi nesciunt. Neque porro quisquam est, qui dolorem ipsum quia dolor sit amet, consectetur, adipisci velit, sed quia non numquam eius modi tempora incidunt ut labore et dolore magnam aliquam quaerat voluptatem.</p>
<div class="abs about-img" role="img" aria-label="Black semi truck with a silver trailer"></div>
<div class="abs btn btn-read">READ MORE</div>

<h2 class="abs section-title" style="left:468px;top:774px">Call &amp; Contact Us</h2>

<div class="abs call" style="top:800px">
  <svg class="bg" width="186" height="47"><polygon points="0,0 186,0 186,47 20,47" fill="#000"/></svg>
  <span class="label">Appointments</span><span class="num">1-800 555 0187</span>
  <svg class="icon" width="9" height="14" viewBox="0 0 9 14"><rect x="0.8" y="0.8" width="7.4" height="12.4" rx="1" fill="none" stroke="#fff" stroke-width="1.5"/><circle cx="4.5" cy="11" r="0.8" fill="#fff"/></svg>
</div>
<div class="abs call" style="top:847px">
  <svg class="bg" width="186" height="47"><polygon points="0,0 186,0 186,47 20,47" fill="#121212"/></svg>
  <span class="label">Office</span><span class="num">1-800 555 0163</span>
  <svg class="icon" width="12" height="12" viewBox="0 0 8 8"><path d="M1 1 L3 1 L3.6 2.8 L2.6 3.6 Q3.5 5 4.6 5.6 L5.4 4.6 L7 5.2 L7 7 Q3 7 1 1Z" fill="#fff"/></svg>
</div>
<div class="abs call" style="top:894px">
  <svg class="bg" width="186" height="47"><polygon points="0,0 186,0 186,47 20,47" fill="#2a2a2a"/></svg>
  <span class="label">Resident Services</span><span class="num">CLICK HERE</span>
  <span class="icon" style="font-size:17px;top:10px">?</span>
</div>

<footer class="abs footer">
  <h4 style="left:81px">Quick Links</h4>
  <ul class="links"><li>Home</li><li>About Us</li><li>Services</li><li>Products</li><li>Apply Now</li><li>Contact Us</li></ul>

  <h4 style="left:202px">Testimonials</h4>
  <div class="quote">"Lorem ipsum dolor sit amet, consectetur adipiscing elit, sed do eiusmod tempor incididunt ut labore et dolore magna aliqua. Ut enim ad minim veniam."</div>
  <div class="quote-tail"></div>
  <div class="avatar" role="img" aria-label="Client portrait"></div>
  <div class="author">Sam Reyes,<br>Lorium ipsum</div>

  <h4 style="left:371px">Contact Us</h4>
  <div class="field" style="top:37px">Name</div>
  <div class="field" style="top:63px">Email Id</div>
  <div class="field" style="top:89px;height:43px">Message</div>
  <div class="abs btn btn-submit">Submit</div>

  <h4 style="left:529px">Follow Us</h4>
  <div class="follow" style="top:33px"><span class="sq" style="background:#1f5aa8"></span>Circlepage</div>
  <div class="follow" style="top:56px"><span class="sq" style="background:#29a9e6"></span>Chirpline</div>
  <div class="follow" style="top:77px"><span class="sq" style="background:#d9261c"></span>Clipcast</div>
  <div class="follow" style="top:98px"><span class="sq" style="background:#e5413a"></span>Searchring</div>
</footer>

<div class="abs bottombar">Copyrights © 2017 - All Rights Reserved</div>

</body>
</html>
```